Design some Business Cards for Brightvane

A startup company named Brightvane IT is looking for a business card design. It needs to be modern, with a strong sense of professionalism and creativity. Design would need to be both front and back. No costs will be spared during printing, so incorporate any printing styles, embossing etc. Size needs to be the standard card size.

The design needs to incorporate the logo provided, include phone number, email address, job title, and company website.

Company website is [login to view URL]

Cards would be for:

Marcus Pellow
CEO
Marcus@[login to view URL]
555-402-3391

Lu Brand
COO/CIO
Lu@[login to view URL]
555-734-0615

Tim Wolverhall
V.P. of Design
Tim@[login to view URL]
555-958-2047

Dana Purcell
V.P. of Sales
Dana@[login to view URL]
555-183-7720

```html
<!DOCTYPE html>
<html lang="en">
<head>
<meta charset="UTF-8">
<title>Brightvane IT — Business Cards</title>
<link rel="stylesheet" href="https://fonts.googleapis.com/css2?family=Mulish:wght@400;600;800&display=swap">
<style>
  :root {
    --page-bg: #e9e9ea;
    --card-dark: #3b3b3d;
    --card-dark-emboss: #48484b;
    --brand-blue: #29abe2;
    --brand-blue-emboss: #49baea;
    --text-light: #ffffff;
    --text-muted: #e6e6e6;
  }
  * { box-sizing: border-box; margin: 0; padding: 0; }
  html, body {
    width: 1200px; height: 900px; overflow: hidden;
    background: var(--page-bg);
    font-family: "Mulish", Arial, sans-serif;
  }
  .sheet {
    position: relative; width: 1200px; height: 900px;
    display: flex; align-items: center; justify-content: center; gap: 60px;
  }
  .card {
    position: relative; width: 525px; height: 300px;
    border-radius: 22px; overflow: hidden;
    box-shadow: 0 6px 18px rgba(0,0,0,0.18);
  }

  /* Front (dark) */
  .card--front { background: var(--card-dark); }
  .front__rule {
    position: absolute; left: 44px; top: 0; width: 3px; height: 236px;
    background: var(--brand-blue);
  }
  .front__rule--lower { top: 262px; height: 38px; }
  .front__corner-mark {
    position: absolute; right: 0; top: 22px; width: 18px; height: 26px;
    background: var(--brand-blue);
  }
  .front__wordmark {
    position: absolute; right: 28px; top: 18px;
    font-weight: 800; font-size: 30px; letter-spacing: 0.5px;
    color: var(--card-dark-emboss);
  }
  .front__name {
    position: absolute; left: 60px; top: 106px;
    font-weight: 800; font-size: 25px; color: var(--brand-blue);
  }
  .front__title {
    position: absolute; left: 60px; top: 138px;
    font-weight: 600; font-size: 15px; color: var(--text-light);
  }
  .front__contacts {
    position: absolute; left: 30px; top: 192px; list-style: none;
  }
  .front__contacts li {
    display: flex; align-items: center; gap: 10px;
    height: 26px; font-weight: 600; font-size: 15px; color: var(--text-light);
  }
  .contact-icon { width: 14px; height: 14px; flex: none; }

  /* Back (blue) */
  .card--back { background: var(--brand-blue); }
  .back__wordmark-emboss {
    position: absolute; right: 30px; top: 20px;
    font-weight: 800; font-size: 34px; color: var(--brand-blue-emboss);
  }
  .back__wordmark {
    position: absolute; left: 0; right: 0; top: 112px; text-align: center;
    font-weight: 800; font-size: 46px; color: var(--text-light);
  }
  .back__website {
    position: absolute; left: 0; right: 0; top: 184px; text-align: center;
    font-weight: 800; font-size: 15px; letter-spacing: 4px; color: var(--text-light);
  }
</style>
</head>
<body>
<main class="sheet">
  <section class="card card--front" aria-label="Card front">
    <span class="front__rule"></span>
    <span class="front__rule front__rule--lower"></span>
    <span class="front__corner-mark"></span>
    <div class="front__wordmark">Brightvane.IT</div>
    <h1 class="front__name">Marcus Pellow</h1>
    <p class="front__title">CEO</p>
    <ul class="front__contacts">
      <li>
        <svg class="contact-icon" viewBox="0 0 14 14" aria-hidden="true">
          <rect width="14" height="14" rx="2" fill="#29abe2"/>
          <path d="M4 3.5c0 4 2.5 6.5 6.5 6.5l.5-1.8-1.8-.8-.8 1C7 7.8 6.2 7 5.6 5.6l1-.8-.8-1.8z" fill="#3b3b3d"/>
        </svg>
        555-402-3391
      </li>
      <li>
        <svg class="contact-icon" viewBox="0 0 14 14" aria-hidden="true">
          <rect width="14" height="14" rx="2" fill="#29abe2"/>
          <rect x="3" y="4" width="8" height="6" fill="none" stroke="#3b3b3d" stroke-width="1.2"/>
          <path d="M3 4l4 3.2L11 4" fill="none" stroke="#3b3b3d" stroke-width="1.2"/>
        </svg>
        Marcus@brightvane.IT
      </li>
      <li>
        <svg class="contact-icon" viewBox="0 0 14 14" aria-hidden="true">
          <rect width="14" height="14" rx="2" fill="#29abe2"/>
          <circle cx="7" cy="7" r="4" fill="none" stroke="#3b3b3d" stroke-width="1.2"/>
          <path d="M3 7h8M7 3c-2 2.5-2 5.5 0 8M7 3c2 2.5 2 5.5 0 8" fill="none" stroke="#3b3b3d" stroke-width="1"/>
        </svg>
        www.brightvane.IT
      </li>
    </ul>
  </section>

  <section class="card card--back" aria-label="Card back">
    <div class="back__wordmark-emboss">Brightvane.IT</div>
    <div class="back__wordmark">Brightvane.IT</div>
    <p class="back__website">www.brightvane.IT</p>
  </section>
</main>
</body>
</html>
```